Harbor Crestline (Business Card Design)

Need business cards designed. Something modern, chic, and sleek. Mabye the back of the card should be the navy blue that is in the logo and then just the logo on the back.

Target Market(s)

Those in the hotel, office, and renovation industry

Contact Information for Business Card

1. Logo 2. Dorian Fenwick 3. CEO/Founder 4. Phone: (833) HarbCre / (833) 427-2731 5. Email: dorian@theharborcrestline.com 6. Website: www.theharborcrestline.com

Font styles to use
Other font styles liked:
• Look at the logo font and base the font for everything else off of that.

Colors
0054AA
0677BA
7BADD7
CADEEF
E8F1F8

Requirements
Must have
• Colors that are associated in the logo
Nice to have
• Sleek modern clean and chic design.

```html
<!DOCTYPE html>
<html lang="en">
<head>
<meta charset="utf-8">
<title>Harbor Crestline — Business Card</title>
<link rel="stylesheet" href="https://fonts.googleapis.com/css2?family=Montserrat:wght@500;600&family=Open+Sans:wght@400;700&display=swap">
<style>
  :root {
    --backdrop: #232323;
    --navy: #0d1a42;
    --gold: #c9a245;
    --white: #ffffff;
    --rule: rgba(255, 255, 255, 0.85);
  }
  * { box-sizing: border-box; margin: 0; padding: 0; }
  html, body {
    width: 1200px; height: 780px; overflow: hidden;
    background: var(--backdrop);
  }
  .canvas {
    position: relative; width: 1200px; height: 780px;
    display: flex; align-items: center; justify-content: center; gap: 40px;
  }
  .card {
    position: relative; width: 540px; height: 309px;
    background: var(--navy);
    box-shadow: 0 10px 28px rgba(0, 0, 0, 0.55);
    overflow: hidden;
  }
  .wordmark {
    font-family: "Montserrat", sans-serif; font-weight: 600;
    color: var(--white); text-transform: uppercase;
    letter-spacing: 0.12em; line-height: 1.15;
    display: flex; align-items: flex-start; gap: 10px;
  }
  .wordmark__dot { width: 10px; height: 10px; background: var(--gold); flex: none; margin-top: 0.3em; }

  /* back */
  .card--back { display: flex; align-items: center; justify-content: center; }
  .card--back .wordmark { font-size: 30px; }

  /* front */
  .card--front .wordmark { position: absolute; left: 48px; top: 60px; font-size: 20px; }
  .wordmark__lines { display: block; }
  .identity {
    position: absolute; right: 38px; top: 64px; text-align: right;
    font-family: "Open Sans", sans-serif;
  }
  .identity__name { font-weight: 700; font-size: 28px; line-height: 1.05; color: var(--white); white-space: nowrap; }
  .identity__first { color: var(--gold); }
  .identity__title { font-size: 14px; color: var(--white); margin-top: 4px; }
  .accent-bar {
    position: absolute; right: 0; top: 60px; width: 22px; height: 62px;
    background: var(--gold);
  }
  .divider {
    position: absolute; left: 48px; right: 38px; top: 138px;
    height: 1px; background: var(--rule);
  }
  .contact {
    position: absolute; left: 48px; top: 158px;
    font-family: "Open Sans", sans-serif; font-size: 13.5px;
    color: var(--white); line-height: 1.35;
  }
  .contact__address { margin-bottom: 12px; }
  .contact__list { list-style: none; }
  .contact__item { display: flex; align-items: center; gap: 9px; }
  .contact__icon { width: 13px; height: 13px; flex: none; }
</style>
</head>
<body>
<main class="canvas">
  <section class="card card--back" aria-label="Card back">
    <div class="wordmark"><span class="wordmark__dot"></span>Harbor Crestline</div>
  </section>

  <section class="card card--front" aria-label="Card front">
    <div class="wordmark"><span class="wordmark__dot"></span><span class="wordmark__lines">Harbor<br>Crestline</span></div>

    <div class="identity">
      <p class="identity__name"><span class="identity__first">Dorian</span> Fenwick</p>
      <p class="identity__title">CEO/Founder</p>
    </div>
    <div class="accent-bar"></div>
    <div class="divider"></div>

    <div class="contact">
      <p class="contact__address">4120 Meridian Way<br>Suite 210, Larkfield, MD 20917</p>
      <ul class="contact__list">
        <li class="contact__item">
          <svg class="contact__icon" viewBox="0 0 24 24" aria-hidden="true"><path fill="#c9a245" d="M6.6 10.8a15 15 0 0 0 6.6 6.6l2.2-2.2a1 1 0 0 1 1-.25 11.4 11.4 0 0 0 3.6.57 1 1 0 0 1 1 1V20a1 1 0 0 1-1 1A17 17 0 0 1 3 4a1 1 0 0 1 1-1h3.5a1 1 0 0 1 1 1c0 1.25.2 2.45.57 3.57a1 1 0 0 1-.25 1z"/></svg>
          (833) HarbCre / (833) 427-2731
        </li>
        <li class="contact__item">
          <svg class="contact__icon" viewBox="0 0 24 24" aria-hidden="true"><g fill="none" stroke="#c9a245" stroke-width="2"><circle cx="12" cy="12" r="9"/><path d="M3 12h18M12 3c3 3.2 3 14.8 0 18M12 3c-3 3.2-3 14.8 0 18"/></g></svg>
          www.theharborcrestline.com
        </li>
        <li class="contact__item">
          <svg class="contact__icon" viewBox="0 0 24 24" aria-hidden="true"><g fill="none" stroke="#c9a245" stroke-width="2"><rect x="3" y="6" width="18" height="13"/><path d="M3 6l9 7 9-7"/></g></svg>
          dorian@theharborcrestline.com
        </li>
      </ul>
    </div>
  </section>
</main>
</body>
</html>
```